Carrow Facilities Services Business Card.

We need a card for Carrow Facilities Services with a new look. We also have service and supply partners that we would like to have on the card. Coatrivex is a surface application company, Carrow Facilities is a facilities services business, Bellmont Supply Co is a Facilities supply business, Prevla is a product that we use that powers our business.

```html
<!DOCTYPE html>
<html lang="en">
<head>
<meta charset="utf-8">
<title>Carrow Facilities Services – Business Card</title>
<link rel="stylesheet" href="https://fonts.googleapis.com/css2?family=Fira+Sans:wght@500;700&family=Open+Sans:wght@400;700&family=Roboto:wght@400&display=swap">
<style>
  :root {
    --backdrop: #000000;
    --card: #2f3033;
    --card-edge: #3a3b3f;
    --white: #ffffff;
    --rule: #55575c;
    --brand-blue: #1976c4;
    --coat-blue: #3ca8da;
    --supply-blue: #4a86c8;
    --muted: #e6e6e6;
  }
  * { margin: 0; padding: 0; box-sizing: border-box; }
  html, body { width: 1200px; height: 900px; overflow: hidden; background: var(--backdrop); }
  .stage { position: relative; width: 1200px; height: 900px; }

  .card {
    position: absolute;
    top: 266px;
    width: 458px;
    height: 281px;
    border-radius: 14px;
    background: var(--card);
    box-shadow: inset 0 0 0 1px var(--card-edge);
    overflow: hidden;
  }
  .card--front { left: 137px; }
  .card--back { left: 625px; }

  /* front */
  .front-brand { position: absolute; left: 32px; top: 108px; display: flex; align-items: center; gap: 8px; }
  .brand-dot { width: 40px; height: 40px; border-radius: 50%; background: var(--white); }
  .brand-words { font-family: "Fira Sans", sans-serif; color: var(--white); line-height: 1; }
  .brand-words .brand-name { font-size: 40px; font-weight: 700; letter-spacing: -0.5px; }
  .brand-words .brand-sub { font-size: 14px; font-weight: 500; margin-top: 4px; }

  .front-rule { position: absolute; left: 229px; top: 67px; width: 1px; height: 145px; background: var(--rule); }

  .contact { position: absolute; left: 248px; top: 72px; color: var(--white); font-family: "Roboto", sans-serif; }
  .contact .person-name { font-family: "Open Sans", sans-serif; font-weight: 700; font-size: 16px; line-height: 18px; }
  .contact .person-role { font-family: "Open Sans", sans-serif; font-size: 13.5px; line-height: 17px; margin-bottom: 9px; }
  .contact .line { display: flex; align-items: center; gap: 5px; font-size: 14px; line-height: 17.5px; }
  .contact .line svg { width: 14px; height: 14px; flex: none; }
  .contact .address { font-size: 14px; line-height: 17px; margin-top: 9px; }

  /* back */
  .back-brand { position: absolute; left: 98px; top: 64px; display: flex; align-items: center; gap: 12px; }
  .back-brand .brand-dot { width: 62px; height: 62px; background: var(--brand-blue); }
  .back-brand .brand-words { color: var(--brand-blue); }
  .back-brand .brand-name { font-size: 58px; font-weight: 700; letter-spacing: -0.5px; }
  .back-brand .brand-sub { font-size: 20px; font-weight: 700; margin-top: 2px; }

  .partners { position: absolute; left: 0; right: 0; top: 200px; display: flex; justify-content: center; align-items: flex-end; gap: 20px; font-family: "Fira Sans", sans-serif; }
  .partner { display: flex; align-items: center; gap: 6px; }
  .partner-name { font-weight: 700; font-size: 14px; line-height: 1; }
  .partner--coat .partner-name { color: var(--coat-blue); }
  .partner--supply .partner-name { color: var(--supply-blue); font-size: 12px; }
  .partner--supply .partner-mark { width: 18px; height: 18px; border-radius: 50%; background: var(--supply-blue); }
  .partner--power { flex-direction: column; align-items: flex-start; gap: 2px; }
  .partner--power .powered { font-family: "Open Sans", sans-serif; font-size: 8.5px; color: var(--muted); }
  .partner--power .partner-name { color: var(--white); font-size: 18px; }
</style>
</head>
<body>
<main class="stage">
  <section class="card card--front" aria-label="Card front">
    <div class="front-brand">
      <span class="brand-dot"></span>
      <div class="brand-words">
        <div class="brand-name">Carrow</div>
        <div class="brand-sub">Facilities Services</div>
      </div>
    </div>
    <div class="front-rule"></div>
    <div class="contact">
      <div class="person-name">DANIEL REYES</div>
      <div class="person-role">Managing Director</div>
      <div class="line">
        <svg viewBox="0 0 24 24" fill="none" stroke="#fff" stroke-width="2"><path d="M5 3h4l2 5-3 2a12 12 0 0 0 6 6l2-3 5 2v4a2 2 0 0 1-2 2A17 17 0 0 1 3 5a2 2 0 0 1 2-2z"/></svg>
        <span>044-987 210 345</span>
      </div>
      <div class="line">
        <svg viewBox="0 0 24 24" fill="none" stroke="#fff" stroke-width="2"><rect x="2" y="5" width="20" height="14"/><path d="M2 5l10 8 10-8"/></svg>
        <span>hello@carrowfs.com</span>
      </div>
      <div class="line">
        <svg viewBox="0 0 24 24" fill="none" stroke="#fff" stroke-width="2"><circle cx="12" cy="12" r="10"/><path d="M2 12h20M12 2c3 3 3 17 0 20M12 2c-3 3-3 17 0 20"/></svg>
        <span>www.carrowfs.com</span>
      </div>
      <div class="address">58 Linden Park Road<br>Northfield, 60318</div>
    </div>
  </section>

  <section class="card card--back" aria-label="Card back">
    <div class="back-brand">
      <span class="brand-dot"></span>
      <div class="brand-words">
        <div class="brand-name">Carrow</div>
        <div class="brand-sub">Facilities Services</div>
      </div>
    </div>
    <div class="partners">
      <div class="partner partner--coat"><span class="partner-name">COATRIVEX</span></div>
      <div class="partner partner--supply"><span class="partner-mark"></span><span class="partner-name">BELLMONT SUPPLY CO</span></div>
      <div class="partner partner--power"><span class="powered">Powered by</span><span class="partner-name">PREVLA</span></div>
    </div>
  </section>
</main>
</body>
</html>
```